Casa Morellina Togo Menu seperated in categories

new to go menu for italian restaurant with menu descriptions and prices i like the cover first page to have all the restaurant information, the other pages should be separated in the menu categories, and if we can include a map with the location of the restaurant
Casa Morellina
42 Route 83 S
North Myrtle Beach, SC 29582
open 7 days a week 4-10
Happy hour served Daily at the Bar 4-7
www.casamorellina.com
casamorellinadine@maildrop.example

Restaurant

Sans Serif

Must have
• Prices and pictures and restaurant information

```html
<!DOCTYPE html>
<html lang="en">
<head>
<meta charset="utf-8">
<title>Pasta Menu</title>
<link href="https://fonts.googleapis.com/css2?family=Oswald:wght@400;500&family=Open+Sans:wght@400&display=swap" rel="stylesheet">
<style>
  :root {
    --red: #a3232d;
    --ink: #1f1f1f;
    --paper: #ffffff;
    --wave-blue: #2f4f86;
  }
  * { margin: 0; padding: 0; box-sizing: border-box; }
  html, body { width: 667px; height: 1200px; overflow: hidden; background: var(--paper); }
  .menu-page {
    position: absolute; left: 39px; top: 40px; width: 590px; height: 1123px;
    border: 2px solid var(--red); background: var(--paper); overflow: hidden;
    font-family: "Open Sans", Arial, sans-serif; color: var(--ink);
  }
  .section-title {
    position: absolute; left: 29px; top: 52px;
    font-family: "Oswald", "Arial Narrow", sans-serif; font-weight: 500;
    font-size: 64px; line-height: 1; letter-spacing: 0.5px; transform: scaleY(1.05);
  }
  .section-note {
    position: absolute; left: 191px; top: 64px; width: 160px;
    font-size: 8px; line-height: 10.5px;
  }
  .extras { position: absolute; left: 384px; top: 62px; width: 166px; font-size: 10.5px; line-height: 13px; }
  .extra { display: flex; justify-content: space-between; align-items: baseline; margin-bottom: 9px; }
  .extra-price { color: var(--red); font-family: "Oswald", sans-serif; font-size: 13px; }
  .dish { position: absolute; left: 29px; width: 520px; }
  .dish-line { display: flex; align-items: baseline; }
  .dish-name {
    font-family: "Oswald", "Arial Narrow", sans-serif; font-weight: 500;
    font-size: 19px; line-height: 24px; white-space: nowrap;
  }
  .dish-name.small { font-family: "Open Sans", sans-serif; font-weight: 400; font-size: 13.5px; }
  .leader { flex: 1; margin: 0 6px; border-bottom: 1.3px dashed var(--red); transform: translateY(-5px); }
  .dish-price { font-family: "Oswald", sans-serif; font-size: 19px; color: var(--red); }
  .dish-desc { font-size: 13.5px; line-height: 18px; padding-right: 10px; }
  .photo-strip { position: absolute; left: 0; bottom: 0; width: 590px; height: 140px; }
  .photo { position: absolute; bottom: 0; height: 118px; }
  .photo-penne { left: 2px; width: 198px; background: radial-gradient(circle at 45% 50%, #e2b57c, #b76f3a 55%, #4a3324); }
  .photo-meatballs { left: 203px; width: 183px; background: radial-gradient(circle at 50% 45%, #8c2a1d, #5a1a12 50%, #1c1414); }
  .photo-fettuccine { left: 389px; width: 198px; background: radial-gradient(circle at 50% 50%, #efe2c6, #cdb58e 55%, #6d6050); }
  .wave { position: absolute; left: 0; top: 0; }
</style>
</head>
<body>
<main class="menu-page">
  <h1 class="section-title">PASTA</h1>
  <p class="section-note">All of our Pasta Dishes served with fresh baked bread and our roasted red pepper, garlic and herb dipping oil, your choice of soup of the day or house salad,</p>
  <div class="extras">
    <div class="extra"><span>Upgrade to Caesar Salad</span><span class="extra-price">1.95</span></div>
    <div class="extra"><span>Split Entrée includes<br>additional soup or salad</span><span class="extra-price">7.00</span></div>
  </div>

  <div class="dish" style="top:145px"><div class="dish-line"><span class="dish-name">Gnocchi Ala Cremina</span><span class="leader"></span><span class="dish-price">13.95</span></div><p class="dish-desc">Potato Dumplings tossed in a Creamy Marinara sauce and Mozzarella</p></div>
  <div class="dish" style="top:209px"><div class="dish-line"><span class="dish-name">Cheese Ravioli</span><span class="leader"></span><span class="dish-price">13.95</span></div><p class="dish-desc">Traditional style Ravioli stuffed with Ricotta, Parmesan and Romano cheese, served with our homemade Marinara Sauce</p></div>
  <div class="dish" style="top:292px"><div class="dish-line"><span class="dish-name">Manicotti</span><span class="leader"></span><span class="dish-price">13.95</span></div><p class="dish-desc">Flat pasta wrapped around four cheeses, topped with fresh Mozzarella, baked with our homemade Marinara sauce</p></div>
  <div class="dish" style="top:374px"><div class="dish-line"><span class="dish-name">Lasagna</span><span class="leader"></span><span class="dish-price">15.95</span></div><p class="dish-desc">Layers of flat pasta, Ricotta cheese, Ground Beef, in our Marinara sauce, topped with fresh Mozzarella</p></div>
  <div class="dish" style="top:454px"><div class="dish-line"><span class="dish-name">Spaghetti Marinara</span><span class="leader"></span><span class="dish-price">11.95</span></div><p class="dish-desc">Spaghetti with our homemade Marinara sauce</p></div>
  <div class="dish" style="top:518px"><span class="dish-name" style="display:block">Choice of Homemade Meatballs,</span><div class="dish-line" style="margin-top:3px"><span class="dish-name">Mild Italian Sausage or Bolognese</span><span class="leader"></span><span class="dish-price">15.95</span></div></div>
  <div class="dish" style="top:596px"><div class="dish-line"><span class="dish-name">Spaghetti Carbonara</span><span class="leader"></span><span class="dish-price">16.95</span></div><p class="dish-desc">Spaghetti tossed in a creamy sauce with onions and Prosciutto</p></div>
  <div class="dish" style="top:654px"><div class="dish-line"><span class="dish-name">Eggplant Rollatini</span><span class="leader"></span><span class="dish-price">16.95</span></div><p class="dish-desc">Eggplant wrapped around Ricotta and Parmesan cheese, topped with fresh Mozzarella, baked with our marinara sauce, served over penne pasta</p></div>
  <div class="dish" style="top:735px"><div class="dish-line"><span class="dish-name">Wild Mushroom Ravioli</span><span class="leader"></span><span class="dish-price">17.95</span></div><p class="dish-desc">Mushroom ravioli in a creamy Gorgonzola sauce with sundried tomatoes and mushrooms</p></div>
  <div class="dish" style="top:815px"><div class="dish-line"><span class="dish-name">Lobster Ravioli</span><span class="leader"></span><span class="dish-price">19.95</span></div><p class="dish-desc">Ravioli stuffed with Lobster in a vodka sauce with Shrimp chunks</p></div>
  <div class="dish" style="top:876px"><div class="dish-line"><span class="dish-name">Fettuccine Alfredo</span><span class="leader"></span><span class="dish-price">14.95</span></div><p class="dish-desc">Fettuccine pasta tossed in our homemade Alfredo sauce</p>
    <div class="dish-line"><span class="dish-name small">With Chicken</span><span class="leader"></span><span class="dish-price">17.95</span></div>
    <div class="dish-line"><span class="dish-name small">With Shrimp</span><span class="leader"></span><span class="dish-price">19.95</span></div>
  </div>

  <div class="photo-strip">
    <div class="photo photo-penne" role="img" aria-label="Photo of penne pasta in a creamy sauce"></div>
    <div class="photo photo-meatballs" role="img" aria-label="Photo of spaghetti with homemade meatballs"></div>
    <div class="photo photo-fettuccine" role="img" aria-label="Photo of fettuccine carbonara with prosciutto"></div>
    <svg class="wave" width="590" height="30" viewBox="0 0 590 30" aria-hidden="true">
      <path d="M0 14 C150 2 300 30 590 4 L590 30 L0 30 Z" fill="var(--wave-blue)"/>
      <path d="M0 10 C150 -2 300 26 590 0 L590 24 C300 30 150 6 0 20 Z" fill="var(--red)"/>
      <path d="M0 0 L590 0 L590 0 C300 26 150 -2 0 10 Z" fill="var(--paper)"/>
    </svg>
  </div>
</main>
</body>
</html>
```